I need a SEO-friendly Wordpress website (making sure to style H1, H2, H3, etc correctly) for a Hawaii-based law firm called Meridian Crest Legal Group. Comparable websites include https://brvlaw.example/ and https://www.lomrit.example/ for design reference. The current copy on the TarnAdvocate.example website can be used.

```html
<!DOCTYPE html>
<html lang="en">
<head>
<meta charset="utf-8">
<title>Meridian Crest Legal Group</title>
<link href="https://fonts.googleapis.com/css2?family=Tinos:wght@400;700&family=Oswald:wght@600&family=Mulish:wght@400;600;700&display=swap" rel="stylesheet">
<style>
:root{
  --orange:#b35f0a;
  --brown:#822c04;
  --deep:#7a2a05;
  --ink:#111;
  --text:#444;
  --white:#fff;
}
*{margin:0;padding:0;box-sizing:border-box}
html,body{width:1200px;height:2432px;overflow:hidden;background:var(--white);font-family:'Mulish',sans-serif;color:var(--text)}
.page{position:relative;width:1200px;height:2432px}
.abs{position:absolute}
/* header */
.site-header{position:absolute;left:0;top:0;width:1200px;height:94px;background:var(--white)}
.brand{position:absolute;left:79px;top:30px;font-family:'Tinos',serif;font-weight:700;font-size:25px;color:var(--ink)}
.main-nav{position:absolute;left:421px;top:39px;display:flex;gap:30px;font-size:14px;font-weight:600;color:#222;letter-spacing:.2px}
.main-nav .active{color:var(--orange);display:flex;align-items:center;gap:6px}
.call-box{position:absolute;left:951px;top:0;width:249px;height:94px;background:var(--orange);color:var(--white)}
.call-box svg{position:absolute;left:22px;top:26px}
.call-box .label{position:absolute;left:70px;top:24px;font-size:14px}
.call-box .num{position:absolute;left:70px;top:44px;font-family:'Tinos',serif;font-weight:700;font-size:22px}
/* hero */
.hero{position:absolute;left:0;top:94px;width:1200px;height:583px;background:linear-gradient(90deg,#3a3f49 0%,#4a4f58 40%,#7d7a76 70%,#5c5a5c 100%)}
.hero-shade{position:absolute;inset:0;background:linear-gradient(90deg,rgba(20,22,28,.55),rgba(20,22,28,.1))}
.hero .kicker{position:absolute;left:79px;top:186px;font-size:19px;color:var(--white)}
.hero h1{position:absolute;left:79px;top:228px;font-family:'Oswald',sans-serif;font-weight:600;font-size:52px;line-height:63px;color:var(--white);letter-spacing:-.5px}
.btn{position:absolute;display:flex;align-items:center;gap:14px;padding-left:26px;height:52px;background:var(--deep);color:var(--white);font-family:'Tinos',serif;font-weight:700;font-size:19px;letter-spacing:.5px}
.slide-arrow{position:absolute;top:350px;width:34px;height:72px}
/* practice */
.section-title{position:absolute;width:1200px;text-align:center;font-family:'Tinos',serif;font-weight:700;color:var(--ink)}
.section-sub{position:absolute;width:1200px;text-align:center;font-size:15px;color:#222}
.area{position:absolute;top:852px;width:240px;text-align:center}
.area .ico{display:block;margin:0 auto}
.area h3{margin-top:30px;font-family:'Tinos',serif;font-weight:400;font-size:22px;color:var(--ink)}
.area p{margin-top:14px;font-size:13.5px;line-height:26px;color:var(--text)}
.area a{display:inline-block;margin-top:9px;font-size:14px;font-weight:700;font-style:italic;color:var(--orange);text-decoration:underline}
/* about */
.gavel-bg{position:absolute;left:0;top:1568px;width:1200px;height:416px;background:radial-gradient(ellipse at 45% 75%,#4a3a2c 0%,#2a2520 45%,#1c1b1a 100%)}
.about-box{position:absolute;left:91px;top:1287px;width:1020px;height:468px;background:var(--orange)}
.about-box h2{position:absolute;left:40px;top:64px;font-family:'Tinos',serif;font-weight:700;font-size:40px;line-height:47px;color:var(--white)}
.about-box h4{position:absolute;left:40px;top:172px;font-size:16px;font-weight:700;color:var(--white)}
.about-box p{position:absolute;left:41px;top:216px;width:460px;font-size:13.5px;line-height:27px;color:#f6dcc0}
.about-photo{position:absolute;left:668px;top:1219px;width:406px;height:469px;background:linear-gradient(180deg,#cfd7d9 0%,#b9c3c6 45%,#6f7d84 60%,#a59a88 85%,#8c7b66 100%)}
/* footer */
.site-footer{position:absolute;left:0;top:1984px;width:1200px;height:448px;background:var(--brown);color:var(--white)}
.site-footer h2{position:absolute;width:1200px;top:58px;text-align:center;font-family:'Tinos',serif;font-weight:700;font-size:31px}
.contact-strip{position:absolute;left:209px;top:132px;width:782px;height:104px;border:1px solid var(--orange);display:flex}
.contact-strip .cell{position:relative;height:100%;border-right:1px solid var(--orange)}
.contact-strip .cell:last-child{border-right:none}
.contact-strip svg{position:absolute}
.contact-strip .txt{position:absolute;font-size:13.5px;line-height:25px;color:#f3dccb}
.contact-strip .txt b{font-weight:700;color:var(--white)}
.mail-round{position:absolute;left:565px;top:260px;width:52px;height:52px;border:1px solid var(--orange);border-radius:50%}
.footer-links{position:absolute;top:334px;width:1200px;text-align:center;font-size:14px;color:#f3dccb}
.footer-links span{padding:0 8px}
.copyright{position:absolute;top:364px;width:1200px;text-align:center;font-size:13.5px;color:#f3dccb}
</style>
</head>
<body>
<div class="page">
  <header class="site-header">
    <div class="brand">Meridian Crest Legal Group</div>
    <nav class="main-nav">
      <span class="active">HOME <svg width="13" height="9" viewBox="0 0 13 9"><path d="M0 0h13L6.5 9z" fill="#b35f0a"/></svg></span>
      <span>PRACTIE AREAS</span><span>ATTORNEY</span><span>BLOG</span><span>CONTACT US</span>
    </nav>
    <div class="call-box">
      <svg width="40" height="40" viewBox="0 0 24 24"><path d="M6.6 10.8a15.1 15.1 0 0 0 6.6 6.6l2.2-2.2c.3-.3.7-.4 1-.2 1.1.4 2.3.6 3.6.6.6 0 1 .4 1 1V20c0 .6-.4 1-1 1A17 17 0 0 1 3 4c0-.6.4-1 1-1h3.5c.6 0 1 .4 1 1 0 1.3.2 2.5.6 3.6.1.3 0 .7-.2 1z" fill="#fff"/></svg>
      <div class="label">Call Us Today :</div>
      <div class="num">+1.808.555.0147</div>
    </div>
  </header>

  <section class="hero" role="img" aria-label="Photo of a couple reviewing legal papers at a laptop">
    <div class="hero-shade"></div>
    <p class="kicker">Over 70 years of combined practice, specializing in:</p>
    <h1>Personal Injury Family &amp;<br>Divorce Child Custody</h1>
    <a class="btn" style="left:77px;top:374px;width:218px">LEARN MORE <svg width="36" height="12" viewBox="0 0 36 12"><path d="M0 6h34M29 1l5 5-5 5" stroke="#d98a3a" stroke-width="1.5" fill="none"/></svg></a>
    <svg class="slide-arrow" style="left:0" viewBox="0 0 34 72"><path d="M0 0 34 36 0 72z" fill="#b35f0a"/><path d="M15 29 9 36l6 7" stroke="#fff" stroke-width="2.5" fill="none"/></svg>
    <svg class="slide-arrow" style="left:1166px" viewBox="0 0 34 72"><path d="M34 0 0 36l34 36z" fill="#b35f0a"/><path d="M19 29l6 7-6 7" stroke="#fff" stroke-width="2.5" fill="none"/></svg>
  </section>

  <h2 class="section-title" style="top:736px;font-size:40px">Our Practice Areas</h2>
  <p class="section-sub" style="top:792px">Dedicated to making sure you receive the care and attention you need.</p>

  <div class="area" style="left:91px">
    <svg class="ico" width="124" height="124" viewBox="0 0 124 124"><circle cx="62" cy="62" r="59" fill="#7a2a05" stroke="#b35f0a" stroke-width="5"/><circle cx="62" cy="70" r="20" fill="none" stroke="#fff" stroke-width="3"/><path d="M54 36l8-8 8 8-8 10z" fill="none" stroke="#fff" stroke-width="3"/></svg>
    <h3>Family &amp; Divorce</h3>
    <p>Our lawyers handle all aspects of<br>family law on the Big Island and<br>neighboring islands.</p>
    <a>Read More</a>
  </div>
  <div class="area" style="left:353px">
    <svg class="ico" width="124" height="124" viewBox="0 0 124 124"><circle cx="62" cy="62" r="59" fill="#7a2a05" stroke="#b35f0a" stroke-width="5"/><circle cx="62" cy="34" r="7" fill="none" stroke="#fff" stroke-width="2.5"/><rect x="48" y="44" width="28" height="24" fill="none" stroke="#fff" stroke-width="2.5"/><path d="M30 80h40l22-10M30 90h62" stroke="#fff" stroke-width="2.5" fill="none"/></svg>
    <h3>Personal Injury</h3>
    <p>Dealing with personal injury and<br>wrongful death claims is hard<br>enough, so the lawyers .</p>
    <a>Read More</a>
  </div>
  <div class="area" style="left:609px">
    <svg class="ico" width="124" height="124" viewBox="0 0 124 124"><circle cx="62" cy="62" r="59" fill="#7a2a05" stroke="#b35f0a" stroke-width="5"/><circle cx="42" cy="38" r="8" fill="none" stroke="#fff" stroke-width="2.5"/><path d="M30 62c2-10 22-10 24 0" stroke="#fff" stroke-width="2.5" fill="none"/><rect x="54" y="52" width="38" height="36" fill="none" stroke="#fff" stroke-width="2.5"/><path d="M52 44h40M60 64h26M60 72h18M60 80h26" stroke="#fff" stroke-width="2" fill="none"/></svg>
    <h3>Corporate &amp; IP</h3>
    <p>The attorneys at MCLG have been<br>helping Big Island business owners<br>with all their legal.</p>
    <a>Read More</a>
  </div>
  <div class="area" style="left:872px">
    <svg class="ico" width="124" height="124" viewBox="0 0 124 124"><circle cx="62" cy="62" r="59" fill="#7a2a05" stroke="#b35f0a" stroke-width="5"/><rect x="38" y="30" width="24" height="60" fill="none" stroke="#fff" stroke-width="2.5"/><rect x="62" y="52" width="26" height="38" fill="none" stroke="#fff" stroke-width="2.5"/><path d="M44 40h12M44 50h12M44 60h12M44 70h12M68 62h14M68 72h14M68 82h14" stroke="#fff" stroke-width="2"/></svg>
    <h3>Real Estate</h3>
    <p>Our lawyers work with home owne-<br>rs, buyers and property developers<br>to ensure timely.</p>
    <a>Read More</a>
  </div>

  <div class="gavel-bg" role="img" aria-label="Dark photo of a wooden judge's gavel"></div>
  <section class="about-box">
    <h2>About The Kona<br>Lawyers Of MCLG</h2>
    <h4>Lawyers Serving the Big Island and Neighboring Islands</h4>
    <p>The experienced attorneys in the Meridian Crest Legal Group's Kailua Kona, Hawaii office provide clients with a wide range of litigation expertise, including legal claims involving divorce &amp; family, personal injury, toxic exposures, intellectual property, and real estate.</p>
    <a class="btn" style="left:40px;top:345px;width:219px">LEARN MORE <svg width="36" height="12" viewBox="0 0 36 12"><path d="M0 6h34M29 1l5 5-5 5" stroke="#d98a3a" stroke-width="1.5" fill="none"/></svg></a>
  </section>
  <div class="about-photo" role="img" aria-label="Photo of a family holding hands at the beach shoreline"></div>

  <footer class="site-footer">
    <h2>Meridian Crest Legal Group</h2>
    <div class="contact-strip">
      <div class="cell" style="width:267px">
        <svg style="left:22px;top:18px" width="26" height="36" viewBox="0 0 26 36"><path d="M13 34S2 20 2 12a11 11 0 0 1 22 0c0 8-11 22-11 22z" fill="none" stroke="#b35f0a" stroke-width="1.8"/><circle cx="13" cy="12" r="4" fill="none" stroke="#b35f0a" stroke-width="1.8"/></svg>
        <div class="txt" style="left:60px;top:12px">48-2210 Ahiki Road,<br>Suite 310 Kailua Kona,<br>Hawaii 96740.</div>
      </div>
      <div class="cell" style="width:248px">
        <svg style="left:30px;top:24px" width="26" height="30" viewBox="0 0 24 24"><path d="M6.6 10.8a15.1 15.1 0 0 0 6.6 6.6l2.2-2.2c.3-.3.7-.4 1-.2 1.1.4 2.3.6 3.6.6.6 0 1 .4 1 1V20c0 .6-.4 1-1 1A17 17 0 0 1 3 4c0-.6.4-1 1-1h3.5c.6 0 1 .4 1 1 0 1.3.2 2.5.6 3.6.1.3 0 .7-.2 1z" fill="none" stroke="#b35f0a" stroke-width="1.3"/></svg>
        <div class="txt" style="left:62px;top:20px">Call Us :<br><b>+1.808.555.0147</b></div>
      </div>
      <div class="cell" style="width:265px">
        <svg style="left:24px;top:28px" width="40" height="26" viewBox="0 0 40 26"><rect x="1" y="1" width="38" height="24" fill="none" stroke="#b35f0a" stroke-width="1.8"/><path d="M1 1l19 14L39 1M1 25l14-12M39 25 25 13" stroke="#b35f0a" stroke-width="1.8" fill="none"/></svg>
        <div class="txt" style="left:74px;top:20px">Email Us :<br>clients@tarnadvocate.example</div>
      </div>
    </div>
    <div class="mail-round"><svg style="position:absolute;left:16px;top:18px" width="20" height="15" viewBox="0 0 20 15"><rect width="20" height="15" rx="1.5" fill="#b35f0a"/><path d="M0 1l10 7 10-7" stroke="#822c04" stroke-width="1.6" fill="none"/></svg></div>
    <div class="footer-links"><span>Home</span>|<span>Practice Area</span>|<span>Attorney</span>|<span>Blog</span>|<span>Contact Us</span></div>
    <div class="copyright">©2019 Meridian Crest Legal Group. - All Rights Reserved. Privacy Policy &nbsp;| Tearms &amp; Condition</div>
  </footer>
</div>
</body>
</html>
```